Satchel & Sundial needs new business card design

I need a new business card design. I'm looking for out-of-the-box design which represents the freedom of being a location independent entrepreneur.
I offer coaching, retreats and trips.
I would like to see designs with and without the photo.
Colors I use are black (#000000), green (#25A796) and brown (#D7C38C)
Website satchelandsundial.example

Target Market(s)

location independent entrepreneurs, digital nomads, people looking to swap the 9 to 5 for a lifestyle business

Industry/Entity Type

Business

Contact Information for Business Card

Dorota Falkner
Your Lifestyle Business Coach, Retreat & Trip Leader
http://satchelandsundial.example
hello@satchelandsundial.example
Live a life you don't need a holiday from

Font styles to use
Serif
Sans Serif

Requirements
Must have
• One side should contain only the logo. I would also consider having the "Live a life you don't need a holiday from" on that side too (depending on how it looks)
• Please show both sides on the designs.

```html
<!DOCTYPE html>
<html lang="en">
<head>
<meta charset="utf-8">
<title>Satchel &amp; Sundial – Business Card</title>
<link rel="stylesheet" href="https://fonts.googleapis.com/css2?family=Oswald:wght@300;400;500;600&family=Kaushan+Script&display=swap">
<style>
  :root {
    --ink: #000000;
    --card-black: #141414;
    --teal: #25A796;
    --teal-text: #1f9a8a;
    --sand: #D7C38C;
    --sand-card: #cdbb84;
    --sand-card-dark: #c6b27a;
    --paper: #ffffff;
    --backdrop: #e8e8e8;
  }
  * { margin: 0; padding: 0; box-sizing: border-box; }
  html, body { width: 1200px; height: 576px; overflow: hidden; }
  body {
    background: var(--backdrop);
    position: relative;
    font-family: "Oswald", Arial, sans-serif;
  }
  .card {
    position: absolute;
    top: 138px;
    width: 484px;
    height: 292px;
    border-radius: 8px;
    overflow: hidden;
  }
  /* Back side: logo only */
  .card--back {
    left: 82px;
    background: linear-gradient(180deg, var(--sand-card) 0%, var(--sand-card-dark) 100%);
    display: flex;
    align-items: center;
    justify-content: center;
  }
  .wordmark {
    font-family: "Oswald", Arial, sans-serif;
    font-weight: 500;
    text-transform: uppercase;
    color: var(--ink);
    letter-spacing: 0.5px;
    white-space: nowrap;
  }
  .card--back .wordmark { font-size: 40px; margin-top: -14px; }

  /* Front side: contact details */
  .card--front { left: 602px; background: var(--paper); }
  .card--front .wave { position: absolute; left: 0; top: 0; }
  .identity { position: absolute; left: 29px; top: 32px; }
  .identity__name {
    font-weight: 500;
    font-size: 20px;
    line-height: 1.1;
    text-transform: uppercase;
    color: var(--ink);
  }
  .identity__role {
    font-weight: 400;
    font-size: 11.5px;
    line-height: 1.3;
    color: var(--teal-text);
    margin-top: 6px;
  }
  .card--front .wordmark {
    position: absolute;
    right: 24px;
    top: 34px;
    font-size: 26px;
  }
  .contacts { position: absolute; left: 29px; top: 156px; list-style: none; }
  .contacts li {
    display: flex;
    align-items: center;
    gap: 8px;
    font-weight: 400;
    font-size: 12px;
    color: var(--ink);
    height: 20.5px;
  }
  .contacts .accent { color: var(--teal-text); }
  .contacts svg { flex: none; }
  .social-marks { display: flex; gap: 2px; }
  .social-marks span {
    width: 9px; height: 9px; background: var(--ink); border-radius: 1.5px; display: block;
  }
  .tagline {
    position: absolute;
    right: 24px;
    top: 218px;
    font-family: "Kaushan Script", cursive;
    font-size: 15px;
    line-height: 1.7;
    color: var(--sand);
    text-align: right;
  }
</style>
</head>
<body>

  <section class="card card--back" aria-label="Card back">
    <span class="wordmark">Satchel &amp; Sundial</span>
  </section>

  <section class="card card--front" aria-label="Card front">
    <svg class="wave" width="484" height="292" viewBox="0 0 484 292" aria-hidden="true">
      <path d="M0,246 C70,270 170,272 270,232 C360,196 430,176 484,178 L484,292 L0,292 Z" fill="var(--card-black)"/>
      <path d="M0,232 C90,252 190,262 270,250 C200,260 90,256 0,244 Z" fill="var(--sand)"/>
      <path d="M44,238 C150,252 230,230 300,202 C370,174 430,158 484,158 L484,166 C430,166 372,180 304,208 C234,238 150,254 44,238 Z" fill="var(--teal)"/>
    </svg>

    <div class="identity">
      <h1 class="identity__name">Dorota Falkner</h1>
      <p class="identity__role">Your Lifestyle Business Coach<br>Retreat &amp; Trip Leader</p>
    </div>

    <span class="wordmark">Satchel &amp; Sundial</span>

    <ul class="contacts">
      <li>
        <svg width="11" height="8" viewBox="0 0 11 8" aria-hidden="true">
          <rect x="0" y="0" width="11" height="8" fill="var(--teal)"/>
          <path d="M0,0 L5.5,4.5 L11,0" stroke="#fff" stroke-width="1.2" fill="none"/>
        </svg>
        hello@satchelandsundial.example
      </li>
      <li>
        <svg width="11" height="11" viewBox="0 0 11 11" aria-hidden="true">
          <circle cx="5.5" cy="5.5" r="5" fill="none" stroke="var(--teal)" stroke-width="1.1"/>
          <ellipse cx="5.5" cy="5.5" rx="2.2" ry="5" fill="none" stroke="var(--teal)" stroke-width="1"/>
          <line x1="0.5" y1="5.5" x2="10.5" y2="5.5" stroke="var(--teal)" stroke-width="1"/>
        </svg>
        <span>www.<span class="accent">satchelandsundial</span>.example</span>
      </li>
      <li>
        <span class="social-marks" aria-hidden="true"><span></span><span></span><span></span></span>
        <span class="accent">/satchelandsundial</span>
      </li>
    </ul>

    <p class="tagline">Live a life you<br>dont need a holiday from</p>
  </section>

</body>
</html>
```